Quillmarsh Property Solutions need a business card design

Hello guys. We would need a business card design asap please.
We are a start up property investment business based in London UK specialised in buying, selling, managing and letting properties and helping distressed property owners.
The name of our Business is Quillmarsh, the logo symbolises the four fundamental elements of the world (earth, air, fire and water) and so it stands for strength, stability, longevity.
We would like the business card to communicate professionalism and reliability. Many many thanks indeed for your work.

Details:

1.) Rosalind Updike
Property Investor
Mobile: +44(0)7700123456
Email: rosalind.quillmarsh@mailbox-example.com

2.) Dominic Updike
Property Investor
Mobile: +44(0)7700987654
Email: dominic.quillmarsh@mailbox-example.com

```html
<!DOCTYPE html>
<html lang="en">
<head>
<meta charset="utf-8">
<title>Quillmarsh Property Solutions – Business Cards</title>
<link rel="stylesheet" href="https://fonts.googleapis.com/css2?family=Jost:wght@500&family=Open+Sans:wght@400&display=swap">
<style>
  :root {
    --page-bg: #d5d5d7;
    --card-bg: #242424;
    --brand-grey: #a3a3a3;
    --ghost-grey: #2f2f2f;
    --red: #d0202a;
    --blue: #2f5dab;
    --green: #1f8a43;
    --text-light: #ffffff;
    --shadow: rgba(0, 0, 0, 0.28);
  }
  * { box-sizing: border-box; margin: 0; padding: 0; }
  html, body {
    width: 883px;
    height: 1200px;
    overflow: hidden;
    background: var(--page-bg);
  }
  .card-stack {
    position: absolute;
    left: 168px;
    top: 283px;
    width: 546px;
    display: flex;
    flex-direction: column;
    gap: 24px;
  }
  .card {
    position: relative;
    width: 546px;
    height: 305px;
    background: var(--card-bg);
    box-shadow: 0 3px 8px var(--shadow);
    overflow: hidden;
  }
  .brand {
    font-family: "Jost", "Futura", sans-serif;
    font-weight: 500;
    color: var(--brand-grey);
    text-transform: uppercase;
    line-height: 1;
  }
  .brand-dot {
    position: absolute;
    border-radius: 50%;
    background: var(--brand-grey);
  }

  /* Front */
  .card-front .brand-dot { width: 26px; height: 26px; left: 260px; top: 82px; }
  .card-front .brand {
    position: absolute;
    left: 0; right: 0;
    top: 166px;
    text-align: center;
  }
  .card-front .brand-name { display: block; font-size: 38px; letter-spacing: 1px; }
  .card-front .brand-tagline { display: block; font-size: 17px; letter-spacing: 1.5px; margin-top: 12px; }

  /* Colour strips */
  .colour-strips {
    position: absolute;
    right: 0;
    bottom: 0;
    display: flex;
    height: 15px;
  }
  .colour-strips span { width: 80px; height: 100%; }
  .strip-green { background: var(--green); }
  .strip-blue { background: var(--blue); }
  .strip-red { background: var(--red); }

  /* Back */
  .ghost-brand {
    position: absolute;
    left: 212px;
    top: 28px;
    font-family: "Jost", "Futura", sans-serif;
    font-weight: 500;
    color: var(--ghost-grey);
    text-transform: uppercase;
    line-height: 1;
  }
  .ghost-brand .brand-name { display: block; font-size: 56px; }
  .ghost-brand .brand-tagline { display: block; font-size: 27px; margin-top: 8px; padding-left: 40px; }

  .card-back .brand-dot { width: 22px; height: 22px; left: 97px; top: 60px; }
  .card-back .brand {
    position: absolute;
    left: 34px;
    top: 134px;
    width: 148px;
    text-align: center;
  }
  .card-back .brand-name { display: block; font-size: 20px; letter-spacing: 0.5px; }
  .card-back .brand-tagline { display: block; font-size: 9.5px; letter-spacing: 0.6px; margin-top: 8px; }

  .contact-bars {
    position: absolute;
    left: 27px;
    top: 180px;
    width: 512px;
    font-family: "Open Sans", "Segoe UI", sans-serif;
    color: var(--text-light);
  }
  .contact-bar {
    display: flex;
    align-items: center;
    padding-left: 21px;
    margin-bottom: 3px;
  }
  .bar-name { background: var(--red); height: 33px; font-size: 16px; }
  .bar-phone { background: var(--blue); height: 19px; font-size: 13px; }
  .bar-email { background: var(--green); height: 19px; font-size: 13px; }
  .bar-name .divider {
    width: 1px; height: 20px; background: var(--text-light);
    margin: 0 10px;
  }
  .bar-name .role { font-size: 13.5px; }
  .contact-icon { width: 12px; height: 12px; margin-right: 11px; flex: none; }
</style>
</head>
<body>
  <main class="card-stack">
    <section class="card card-front" aria-label="Business card front">
      <span class="brand-dot"></span>
      <h1 class="brand">
        <span class="brand-name">Quillmarsh</span>
        <span class="brand-tagline">Property Solutions</span>
      </h1>
      <div class="colour-strips"><span class="strip-green"></span><span class="strip-blue"></span><span class="strip-red"></span></div>
    </section>

    <section class="card card-back" aria-label="Business card back">
      <div class="ghost-brand" aria-hidden="true">
        <span class="brand-name">Quillmarsh</span>
        <span class="brand-tagline">Property Solutions</span>
      </div>
      <span class="brand-dot"></span>
      <h2 class="brand">
        <span class="brand-name">Quillmarsh</span>
        <span class="brand-tagline">Property Solutions</span>
      </h2>
      <div class="contact-bars">
        <div class="contact-bar bar-name">
          <span class="person">Rosalind Updike</span>
          <span class="divider"></span>
          <span class="role">Property Investor</span>
        </div>
        <div class="contact-bar bar-phone">
          <svg class="contact-icon" viewBox="0 0 12 12" aria-hidden="true">
            <rect x="3" y="0.5" width="6" height="11" rx="1" fill="none" stroke="#fff" stroke-width="1"/>
            <rect x="5" y="9.3" width="2" height="1" fill="#fff"/>
          </svg>
          <span>+44(0)7700123456</span>
        </div>
        <div class="contact-bar bar-email">
          <svg class="contact-icon" viewBox="0 0 12 12" aria-hidden="true">
            <rect x="0.5" y="2.5" width="11" height="7" fill="#fff"/>
            <path d="M0.5 2.5 L6 6.5 L11.5 2.5" fill="none" stroke="#1f8a43" stroke-width="1"/>
          </svg>
          <span>rosalind.quillmarsh@mailbox-example.com</span>
        </div>
      </div>
      <div class="colour-strips"><span class="strip-green"></span><span class="strip-blue"></span><span class="strip-red"></span></div>
    </section>
  </main>
</body>
</html>
```